Redesign of business card for Cedar Ridge Mechanical

We are looking for a new design for our business cards for Cedar Ridge Mechanical. We are a plumbing & HVAC construction company, operating on the West Coast of Canada and USA. Logo attached.
Industry/Entity Type
Construction - Plumbing & HVAC
Contact Information for Business Card
Name, address, phone numbers, email, website address
Look and feel
Each slider illustrates characteristics of the customer's brand and the style your logo design should communicate.

```html
<!DOCTYPE html>
<html lang="en">
<head>
<meta charset="utf-8">
<title>Cedar Ridge Mechanical – Business Card</title>
<link rel="stylesheet" href="https://fonts.googleapis.com/css2?family=Montserrat:wght@400;500;700&display=swap">
<style>
  :root {
    --stage: #3a3a3c;
    --paper: #ffffff;
    --ink: #111111;
    --accent-grey: #9a9a9a;
    --divider: #d9d9d9;
  }
  html, body {
    margin: 0;
    padding: 0;
    width: 1200px;
    height: 913px;
    overflow: hidden;
    background: var(--stage);
    font-family: "Montserrat", sans-serif;
  }
  .canvas {
    position: relative;
    width: 1200px;
    height: 913px;
  }
  .card {
    position: absolute;
    width: 560px;
    height: 320px;
    border-radius: 22px;
    overflow: hidden;
    background: var(--paper);
    box-shadow: 0 10px 30px rgba(0,0,0,.35);
  }
  .card-front { left: 60px; top: 90px; }
  .card-back  { left: 580px; top: 500px; }

  .brand {
    display: flex;
    align-items: center;
    gap: 14px;
    color: var(--ink);
    font-weight: 700;
    text-transform: uppercase;
    letter-spacing: .04em;
    white-space: nowrap;
  }
  .brand-square {
    background: var(--ink);
    flex: none;
  }
  .card-front .brand {
    position: absolute;
    inset: 0;
    justify-content: center;
    font-size: 30px;
  }
  .card-front .brand-square { width: 34px; height: 34px; }

  .card-back .back-shape {
    position: absolute;
    inset: 0;
  }
  .card-back .brand {
    position: absolute;
    left: 105px;
    top: 40px;
    font-size: 18px;
    gap: 12px;
  }
  .card-back .brand-square { width: 22px; height: 22px; }

  .person {
    position: absolute;
    left: 40px;
    top: 214px;
    width: 210px;
    text-align: right;
    color: var(--paper);
  }
  .person-name {
    font-size: 20px;
    font-weight: 700;
    letter-spacing: .03em;
    margin: 0;
  }
  .person-role {
    font-size: 14px;
    font-weight: 400;
    margin: 2px 0 0;
  }
  .divider {
    position: absolute;
    left: 268px;
    top: 194px;
    width: 1px;
    height: 74px;
    background: var(--divider);
  }
  .contacts {
    position: absolute;
    left: 286px;
    top: 190px;
    margin: 0;
    padding: 0;
    list-style: none;
    color: var(--paper);
    font-size: 14px;
    line-height: 25px;
  }
  .contacts li { display: flex; align-items: center; gap: 8px; }
  .contacts svg { width: 13px; height: 13px; flex: none; }
  .address {
    position: absolute;
    left: 200px;
    top: 282px;
    margin: 0;
    color: var(--paper);
    font-size: 14px;
  }
</style>
</head>
<body>
<main class="canvas">

  <section class="card card-front" aria-label="Card front">
    <div class="brand"><span class="brand-square"></span>Cedar Ridge Mechanical</div>
  </section>

  <section class="card card-back" aria-label="Card back">
    <svg class="back-shape" viewBox="0 0 560 320" preserveAspectRatio="none" aria-hidden="true">
      <path d="M0 190 Q 330 190 560 60 L560 320 L0 320 Z" fill="var(--ink)"/>
      <path d="M0 182 Q 330 182 560 52" fill="none" stroke="var(--accent-grey)" stroke-width="3"/>
    </svg>

    <div class="brand"><span class="brand-square"></span>Cedar Ridge Mechanical</div>

    <div class="person">
      <p class="person-name">DANIEL HAYES</p>
      <p class="person-role">Managing Director</p>
    </div>

    <span class="divider"></span>

    <ul class="contacts">
      <li>
        <svg viewBox="0 0 16 16" aria-hidden="true"><path fill="#fff" d="M3.6 1.5l2.3 2.6-1.3 1.9c.9 2 2.5 3.6 4.4 4.5l1.9-1.3 2.6 2.3-1.4 2.3C7.6 15.5.5 8.4 1.2 2.9z"/></svg>
        123 456 789
      </li>
      <li>
        <svg viewBox="0 0 16 16" aria-hidden="true"><rect x="1" y="3" width="14" height="10" rx="1" fill="#fff"/><path d="M1.5 3.8L8 9l6.5-5.2" fill="none" stroke="#111" stroke-width="1.2"/></svg>
        info@youremail.com
      </li>
      <li>
        <svg viewBox="0 0 16 16" aria-hidden="true"><circle cx="8" cy="8" r="6.5" fill="none" stroke="#fff" stroke-width="1.4"/><path d="M1.5 8h13M8 1.5c-3 3.5-3 9.5 0 13M8 1.5c3 3.5 3 9.5 0 13" fill="none" stroke="#fff" stroke-width="1.1"/></svg>
        www.yourwebsite.com
      </li>
    </ul>

    <p class="address">Your address, City State, Zip 1234</p>
  </section>

</main>
</body>
</html>
```